Website design for luxury private hair salon

I'm looking for someone to use my Logo and build me a website for my webpage www.corsetresses.com.au (You can have a look at it as it has every detail I need included on it already), however I want a fresh new appearance and it to look and feel super stylish.

I am thinking colours in black, with silver or white, beautiful hair images like the ones you'll see on the current webpage - the price list as per what you already see.

I will include a copy of my biz card on here, so you can see the feel of the card, and design a website with a similar feel. It is matt black with a foil silver.

Modern, but classic and fresh. I will also need you to be able to publish it to my URL for me as I have no idea how to do this. I need it up and running pronto!

The website will need to be able to be read clearly on all devices incluing smart phones and ipads. The URL is currently registered and hosted by Norvel Web

Thinking a Home Page - large logo etc and write up on who and what we offer
Services/Price List page - as per the price list on my current webpage
Contact Page - with a built in contact form.

Target Market(s)

Middle aged, fashionable, stylish women and men who enjoy luxury hair care and styling in an upmarket location.

Industry/Entity Type

Hair And Beauty

Number of Pages Required

3 page

Font styles to use
Other font styles liked:
• see my images for my current logo

Colors
000000
b2b2b2
a54499

Requirements
Must have
• Style
• Fast turnaround
• Be viewable on all devices, PC, ipads, smart phones
• Designer able to upload it so its a running website for me to my URL
Nice to have
• Just a really feminine, stylish website which is easy to read and shows some beautiful images of perfect hair
Should not have
• Browns, reds or orange colours.

```html
<!DOCTYPE html>
<html lang="en">
<head>
<meta charset="utf-8">
<title>Velour hair &amp; body</title>
<link rel="stylesheet" href="https://fonts.googleapis.com/css2?family=Open+Sans:wght@400;700&family=Lato:wght@300;400;700&display=swap">
<style>
  :root {
    --black: #0b0b0b;
    --charcoal: #1c1c1c;
    --silver: #b2b2b2;
    --white: #ffffff;
    --plum: #a54499;
    --mist: #f1f1f1;
    --text-dark: #222222;
  }
  * { margin: 0; padding: 0; box-sizing: border-box; }
  html, body { width: 691px; height: 1200px; overflow: hidden; background: var(--white); }
  body { font-family: "Lato", sans-serif; color: var(--text-dark); }
  .page { position: relative; width: 691px; height: 1200px; overflow: hidden; }
  .backdrop { position: absolute; inset: 0; }

  .nav { position: absolute; top: 0; left: 0; width: 100%; height: 38px; display: flex; justify-content: center; padding-left: 8px; }
  .nav a { font-family: "Open Sans", sans-serif; font-weight: 700; font-size: 8px; color: var(--white); text-decoration: none; height: 38px; line-height: 38px; padding: 0 6px; }
  .nav a.is-active { background: var(--plum); }

  .brand { position: absolute; top: 70px; left: 0; width: 100%; text-align: center; color: var(--white); font-family: "Lato", sans-serif; font-weight: 300; }
  .brand-name { font-size: 92px; line-height: 1; letter-spacing: 2px; }
  .brand-tag { font-size: 20px; letter-spacing: 2px; margin-top: 4px; padding-left: 70px; }

  .section-title { font-family: "Open Sans", sans-serif; font-weight: 700; font-size: 15px; text-align: center; letter-spacing: .3px; }
  .section-title span { color: var(--plum); }

  .welcome { position: absolute; top: 312px; left: 268px; width: 312px; text-align: center; }
  .welcome .section-title { color: var(--text-dark); }
  .welcome p { font-size: 6.4px; line-height: 10px; margin-top: 9px; color: #333333; }
  .welcome .signoff { font-weight: 700; margin-top: 8px; color: var(--text-dark); }

  .services { position: absolute; top: 466px; left: 0; width: 100%; text-align: center; color: var(--white); }
  .services p { font-size: 7px; margin-top: 10px; color: var(--white); }

  .gallery-title { position: absolute; top: 576px; left: 0; width: 100%; color: var(--text-dark); }

  .contact { position: absolute; top: 936px; left: 0; width: 100%; color: var(--white); }
  .contact .section-title { color: var(--white); }
  .contact-form { position: absolute; top: 28px; left: 210px; width: 280px; }
  .field { display: block; width: 100%; font-family: "Lato", sans-serif; font-size: 6.5px; color: #d8d8d8; background: transparent; border: 0; border-bottom: 1px solid #555555; padding: 4px 0 5px; height: 18px; margin-bottom: 7px; }
  .field::placeholder { color: #d8d8d8; }
  .field-message { height: 74px; border: 1px solid #555555; padding: 5px 4px; resize: none; margin-top: 6px; }
  .send { position: absolute; top: 137px; left: 111px; width: 50px; height: 16px; background: var(--plum); color: var(--white); font-family: "Open Sans", sans-serif; font-weight: 700; font-size: 6.5px; border: 0; }
  .appointment { position: absolute; top: 196px; width: 100%; text-align: center; font-weight: 700; font-size: 6.5px; }
  .phones { position: absolute; top: 212px; width: 100%; text-align: center; font-size: 10px; font-weight: 300; letter-spacing: .3px; }
  .phones .divider { margin: 0 10px; }
  .footer-line { position: absolute; top: 239px; width: 100%; text-align: center; font-size: 6px; color: #dddddd; }
</style>
</head>
<body>
<div class="page">
  <svg class="backdrop" width="691" height="1200" viewBox="0 0 691 1200">
    <defs>
      <radialGradient id="heroTone" cx=".62" cy=".35" r=".6">
        <stop offset="0" stop-color="#4a4a4a"/><stop offset=".55" stop-color="#1e1e1e"/><stop offset="1" stop-color="#070707"/>
      </radialGradient>
      <radialGradient id="welcomeTone" cx=".75" cy=".3" r=".7">
        <stop offset="0" stop-color="#ffffff"/><stop offset=".6" stop-color="#f0f0f0"/><stop offset="1" stop-color="#dedede"/>
      </radialGradient>
      <linearGradient id="servicesTone" x1="0" y1="0" x2="0" y2="1">
        <stop offset="0" stop-color="#1a1a1a"/><stop offset=".5" stop-color="#2a2a2a"/><stop offset="1" stop-color="#0a0a0a"/>
      </linearGradient>
      <linearGradient id="portraitTone" x1="0" y1="0" x2="1" y2="1">
        <stop offset="0" stop-color="#1a1018"/><stop offset=".45" stop-color="#6a2c62"/><stop offset="1" stop-color="#b058a6"/>
      </linearGradient>
      <linearGradient id="runnerTone" x1="0" y1="0" x2="0" y2="1">
        <stop offset="0" stop-color="#a9cde6"/><stop offset=".5" stop-color="#8a8f96"/><stop offset="1" stop-color="#3a3a3c"/>
      </linearGradient>
      <linearGradient id="sunsetTone" x1="0" y1="0" x2="0" y2="1">
        <stop offset="0" stop-color="#2e1a2a"/><stop offset=".4" stop-color="#b46a3a"/><stop offset=".55" stop-color="#f0c060"/><stop offset=".75" stop-color="#7d8a34"/><stop offset="1" stop-color="#4a5a22"/>
      </linearGradient>
      <linearGradient id="portraitManTone" x1="0" y1="0" x2="0" y2="1">
        <stop offset="0" stop-color="#dfe1e8"/><stop offset=".5" stop-color="#c6c9d2"/><stop offset=".7" stop-color="#4a4c58"/><stop offset="1" stop-color="#1c2130"/>
      </linearGradient>
      <linearGradient id="friendsTone" x1="0" y1="0" x2="0" y2="1">
        <stop offset="0" stop-color="#d6e6ee"/><stop offset=".45" stop-color="#8fb0c4"/><stop offset=".75" stop-color="#5a7a92"/><stop offset="1" stop-color="#8aa470"/>
      </linearGradient>
      <radialGradient id="sparkTone" cx=".6" cy=".5" r=".7">
        <stop offset="0" stop-color="#e08a6a"/><stop offset=".4" stop-color="#6a3a3a"/><stop offset="1" stop-color="#221820"/>
      </radialGradient>
      <linearGradient id="mapTone" x1="0" y1="0" x2="1" y2="1">
        <stop offset="0" stop-color="#e6e6e6"/><stop offset=".5" stop-color="#d9d9d9"/><stop offset="1" stop-color="#cfcfcf"/>
      </linearGradient>
      <radialGradient id="salonTone" cx=".5" cy=".2" r=".8">
        <stop offset="0" stop-color="#3a3a3a"/><stop offset=".55" stop-color="#1c1c1c"/><stop offset="1" stop-color="#0a0a0a"/>
      </radialGradient>
    </defs>
    <!-- hero -->
    <polygon points="0,0 691,0 691,236 0,292" fill="url(#heroTone)" role="img" aria-label="Monochrome photo of a woman in a fur collar behind the salon name"/>
    <polygon points="0,286 691,230 691,236 0,292" fill="var(--plum)"/>
    <!-- welcome band -->
    <polygon points="0,292 691,236 691,452 0,420" fill="url(#welcomeTone)" role="img" aria-label="Soft pale photo of flowing hair"/>
    <!-- services band -->
    <polygon points="0,416 691,448 691,526 0,565" fill="url(#servicesTone)" role="img" aria-label="Dark blurred salon interior"/>
    <polygon points="0,416 691,448 691,454 0,422" fill="var(--plum)"/>
    <polygon points="330,565 691,526 691,564" fill="var(--plum)"/>
    <!-- gallery tiles -->
    <rect x="0" y="606" width="50" height="132" fill="url(#runnerTone)" role="img" aria-label="Photo of a runner on a mountain road"/>
    <rect x="50" y="606" width="197" height="132" fill="url(#sunsetTone)" role="img" aria-label="Photo of an old truck in a field at sunset"/>
    <rect x="247" y="606" width="198" height="132" fill="url(#portraitManTone)" role="img" aria-label="Photo of a smiling bearded man"/>
    <rect x="445" y="606" width="197" height="132" fill="url(#friendsTone)" role="img" aria-label="Photo of three friends with a bicycle"/>
    <rect x="642" y="606" width="49" height="132" fill="url(#sparkTone)" role="img" aria-label="Photo of sparklers at night"/>
    <!-- map -->
    <polygon points="0,764 691,778 691,786 0,784" fill="var(--plum)"/>
    <rect x="0" y="784" width="691" height="136" fill="url(#mapTone)" role="img" aria-label="Street map showing the salon location"/>
    <rect x="0" y="918" width="691" height="2" fill="var(--plum)"/>
    <!-- contact -->
    <rect x="0" y="920" width="691" height="280" fill="url(#salonTone)" role="img" aria-label="Dark photo of the salon styling stations"/>
    <!-- diamond portrait -->
    <polygon points="174,184 286,296 174,408 62,296" fill="url(#portraitTone)" role="img" aria-label="Purple toned portrait of a woman with a short bob"/>
  </svg>

  <nav class="nav">
    <a class="is-active" href="#">HOME</a>
    <a href="#">SERVICES</a>
    <a href="#">CONTACT</a>
  </nav>

  <div class="brand">
    <div class="brand-name">Velour</div>
    <div class="brand-tag">hair &amp; body</div>
  </div>

  <section class="welcome">
    <h2 class="section-title">WELCOME TO <span>VELOUR</span></h2>
    <p>We pride ourselves on being able to offer a private salon experience to our clients in the exclusive suburb of Ashbury Vale, where your hair design and colouring needs will be met with years of experience and current industry training and knowledge*.</p>
    <p class="signoff">- The Velour Team -</p>
  </section>

  <section class="services">
    <h2 class="section-title">OUR <span>SERVICES</span></h2>
    <p>Hair Cuts - Colouring - Highlighting - Extensions - Straightening - Bridal - Treatments - Products &amp; Advice</p>
  </section>

  <h2 class="section-title gallery-title">OUR <span>GALLERY</span></h2>

  <section class="contact">
    <h2 class="section-title">GET IN <span>TOUCH</span></h2>
    <form class="contact-form">
      <input class="field" type="text" placeholder="Your name...">
      <input class="field" type="email" placeholder="Your email...">
      <textarea class="field field-message" placeholder="Type your message..."></textarea>
      <button class="send" type="button">SEND</button>
    </form>
    <p class="appointment">BY APPOINTMENT ONLY</p>
    <p class="phones">ANA 0400 555 101<span class="divider">|</span>RUE 0400 555 202</p>
    <p class="footer-line">www.corsetresses.com.au - ASHBURY VALE, Western Australia - 6099 - By Appointment Only</p>
  </section>
</div>
</body>
</html>
```